Blood Testing Health App

We are looking for a graphics designer to create a web app for us so that we may insert it into a health management website system.
For branding purposes we are at www.Vantiqor.com and we are revamping our website... Example of new colors attached.
How we work...
We are a blood testing company based in the USA.
We offer a blood testing service nationwide in the USA.
We allow customers to order tests directly from us, visit a lab, have their blood drawn, or submit a urine sample, the lab tests it and they send the results back to our computer system and we share it with the customer.
The benefits of this are the customer does not need to go to the doctor and pay for the doctors visit to order these tests, which save them money. The tests are cheaper than going through the doctor. The customer simply uses us to get the test and the results and they can then take the results to their doctor... this process has saved them money. Others may be interested in regular check ups for blood work etc... and this allows them to do it with out needing a doctor, or if you have no insurance, this is a cheaper option too. We are quicker than a doctor, customers do not need appointments etc.
Hopefully you now have a better understanding as to what we do.
Here is the spec.
The app screen size is 750 px wide by 700 px high. ( A pdf is attached to show where the app is going to go, it is on page 3 of the pdf) The customer will have the ability to scroll… therefore the length of the page can be longer.
The app will consist of the following sections
Entry Page –
This will be the first page the user sees upon opening the app. This will be where they are directed from to the sections of the app discussed below. This needs to be branded for VantiQor with a modern look.
1 – Order Test (Giving them the ability to purchase a blood test within the app)
2 – VantiQor Dashboard (A dashboard that has everything they could need to use our service_
How it works Section on entry page – this will be a simple set of graphics showing how the service works. We already have the graphics for this, they do not need to be built again. They are attached to this brief
Basic structure of sections –
Order Test –
This page contains all tests, filed in categories – and Sub categories – Each test needs a link to an Information section – Price – Buy Now – Cart Process
VantiQor Dashboard –
A page of icons along the top of the app
- My Confirmation
- My Nearest Lab
- My Receipt
- My Orders
- My Account
- My Results
- My Inbox
- Contact Us
Sections in more detail -
Order A Test –
Show all categories/ sub categories – There are 23 categories, 14 sub categories, and within these categories are 300 tests - Here is the information for the categories etc - http://www.vantiqor.com/panels.aspx?PanelGroupID=4 Just in case it helps :)
We need to present this in a graphic format that is spacious, modern (brimlake, kivvo web appearance is the direction we are going for) We need it to be clear and not overwhelming to the customer.
Functionality idea…
Customer clicks category/ subcategory and tests appear.
Customer sees small 35 word description. For more information the test opens into a lightbox or expand the container which ever graphic designer believes to be most visually appealing
Buy Now must always be visible, along with price of the test
Buying process explained – Customer clicks buy now –
They are then taken to a Review Order screen ( This contains Order summary and choose payment method – insert payment details )
– Confirm payment –
Confirmation screen appears, thanking them.
They are then taken to the VantiQor Dashboard...
VantiQor Dashboard –
"My Confirmation" - Print Confirmation Order (PDF is in brief, we want this web based not a pdf download)
"My Nearest Lab Location" - This does not need to be designed because the web developer has this part under control, but we do need the icon in the dashboard
"My Receipt" - Print receipt - This does not exist in our system yet. So we need to create this from scratch - It will need to have - The test they are purchasing and the amount of the test - The customers name - The order ID - Must provide printer friendly option too
"My Orders" - This will have a list of orders - At the end of each order will be a status update of either "Test results" "Open order"
A graphic table format would be perfect. This will be linked to relevant results if they have been received. I have also attached a version of what the customer currently sees on our website. We know it is nasty ;) We are redesigning... but the information is there for this section to help design it with the right info. If the results are ready it will say in this list.
"Results Ready" will be a link to show those results once the customer has clicked the link, and the results will appear in the app, under the icons. There must be a printer friendly version too.
"My Results" Developer will sort this page out but we need the icon... It will be exactly like my orders but only show test results
"My Account" - This will be a place for them to update their personal information - Name, DOB, Address, Email Address
"My Inbox" - An inbox interface - Our way of contacting the customer for promotions we are running etc – We need a design of how this screen will appear. We also need the icon in the dashboard to have a notification on it if there are messages in the customers inbox. A little red 1, or circle with number of messages in the inbox.
"Customer Service" - This does not need to be designed because the web developer has this part under control, but we do need the icon in the dashboard
Icons appear along the top of app ( example - Mac icons/ iphone app icons) When the customer clicks an icon the content always appears below the icons
Here is more information for the icons and what should appear when each icon is clicked.
Screens to be designed –
Entry Page
Order A Test Page
Review Order Screen/Payment Screen - Show a lightbox that shows payment has been confirmed. Customer clicks close and are on the Confirmation Screen
VantiQor Dashboard - Screens mentioned in detail above
We can't wait to see your designs!
Please email any questions.
Hi all this is the first time we have used pixel harbor and understand the budget was too low for this project. We have now increased the budget to $2,000 and extended the deadline by another week
Hi all we are receiving some really great designs. I just added an example of the space that the web app will be going into... It is called "morvelapp.pdf"
Hi guys updated the brief. Hopefully this will help with the dashboard part of the design

```html
<!DOCTYPE html>
<html lang="en">
<head>
<meta charset="utf-8">
<title>VantiQor – My Account</title>
<link href="https://fonts.googleapis.com/css2?family=Open+Sans:wght@400;600;700&display=swap" rel="stylesheet">
<style>
  :root {
    --green: #7dc142;
    --ink: #333333;
    --ink-soft: #444444;
    --muted: #9a9a9a;
    --blue: #1e7ac4;
    --band-top: #d9d9d9;
    --band-bottom: #ededed;
    --panel: #ebebeb;
    --card: #ffffff;
    --field: #f4f4f4;
    --field-line: #dedede;
    --badge: #f04a23;
    --icon: #4a4f52;
  }
  * { box-sizing: border-box; margin: 0; padding: 0; }
  html, body { width: 987px; height: 1200px; overflow: hidden; background: #fff; }
  body { font-family: "Open Sans", Arial, sans-serif; color: var(--ink); }

  .app { position: absolute; left: 0; top: 0; width: 750px; height: 912px; transform: scale(1.316); transform-origin: 0 0; }

  /* header */
  .header { position: absolute; left: 0; top: 0; width: 750px; height: 100px; background: #fff; }
  .brand { position: absolute; left: 18px; top: 46px; font-size: 38px; font-weight: 400; letter-spacing: 1px; color: var(--ink); line-height: 1; }

  .tab { position: absolute; top: 28px; height: 72px; width: 124px; text-align: center; font-size: 11px; letter-spacing: .2px; }
  .tab svg { display: block; margin: 12px auto 6px; }
  .tab-order { left: 338px; color: var(--muted); }
  .tab-dashboard { left: 456px; color: var(--green); background: #e9e9e9; border-radius: 8px 8px 0 0; }

  .social { position: absolute; top: 63px; width: 28px; height: 28px; border-radius: 50%; background: var(--green); }

  /* icon band */
  .nav-band { position: absolute; left: 0; top: 100px; width: 750px; height: 136px; background: linear-gradient(var(--band-top), var(--band-bottom)); }
  .nav-item { position: absolute; top: 30px; width: 92px; margin-left: -46px; text-align: center; font-size: 11.5px; line-height: 1.05; color: var(--ink); }
  .nav-item .bubble { width: 62px; height: 62px; margin: 0 auto 6px; border-radius: 50%; background: radial-gradient(circle at 50% 35%, #ffffff 0%, #f3f3f3 55%, #d4d4d4 100%); box-shadow: 0 2px 3px rgba(0,0,0,.25), inset 0 0 0 1px rgba(0,0,0,.06); display: flex; align-items: center; justify-content: center; }
  .nav-item.is-active { color: var(--blue); }
  .nav-item .badge { position: absolute; left: 64px; top: 4px; min-width: 26px; height: 18px; padding: 0 6px; border-radius: 4px; background: var(--badge); color: #fff; font-size: 11px; line-height: 18px; }
  .nav-pointer { position: absolute; left: 503px; top: 128px; width: 0; height: 0; border-left: 8px solid transparent; border-right: 8px solid transparent; border-bottom: 8px solid #fff; }
  .figure-fill { width: 34px; height: 40px; border-radius: 17px 17px 8px 8px; }

  /* content */
  .panel { position: absolute; left: 17px; top: 262px; width: 712px; height: 598px; background: var(--panel); border-radius: 8px; }
  .card { position: absolute; left: 18px; width: 675px; background: var(--card); border-radius: 8px; }
  .card-info { top: 18px; height: 295px; }
  .card-password { top: 335px; height: 244px; }
  .card-title { position: absolute; left: 28px; top: 20px; font-size: 17px; font-weight: 700; color: var(--ink-soft); }

  .field { position: absolute; height: 32px; border: 1px solid var(--field-line); border-radius: 9px; background: var(--field); font-size: 13.5px; line-height: 30px; padding-left: 16px; color: var(--ink); }
  .select::after { content: ""; position: absolute; right: 12px; top: 11px; border-left: 6px solid transparent; border-right: 6px solid transparent; border-top: 10px solid var(--ink-soft); }

  .radio { position: absolute; top: 191px; font-size: 13.5px; color: var(--ink-soft); display: flex; align-items: center; gap: 5px; }
  .radio i { display: inline-block; width: 13px; height: 13px; border: 1px solid #aaa; border-radius: 50%; background: #fafafa; position: relative; }
  .radio.is-checked i::after { content: ""; position: absolute; left: 3px; top: 3px; width: 5px; height: 5px; border-radius: 50%; background: #333; }

  .field-label { position: absolute; left: 34px; font-size: 13.5px; color: var(--ink-soft); }

  .button { position: absolute; width: 199px; height: 39px; border-radius: 6px; background: linear-gradient(#f2f2f0, #cfcfcb); box-shadow: 0 1px 2px rgba(0,0,0,.3); font-size: 18px; font-weight: 700; color: #555; text-align: center; line-height: 37px; }
</style>
</head>
<body>
<div class="app">

  <header class="header">
    <div class="brand">VANTIQOR</div>

    <div class="tab tab-order">
      <svg width="30" height="22" viewBox="0 0 30 22"><rect x="5" y="1" width="20" height="14" rx="2" fill="#a7a7a7"/><rect x="1" y="16" width="28" height="4" rx="1.5" fill="#a7a7a7"/></svg>
      ORDER A TEST
    </div>
    <div class="tab tab-dashboard">
      <svg width="26" height="24" viewBox="0 0 26 24"><rect x="7" y="1" width="17" height="14" fill="none" stroke="#7dc142" stroke-width="2.4"/><rect x="2" y="7" width="17" height="15" fill="#fff" stroke="#7dc142" stroke-width="2.4"/></svg>
      DASHBOARD
    </div>

    <span class="social" style="left:627px"></span>
    <span class="social" style="left:665px"></span>
    <span class="social" style="left:704px"></span>
  </header>

  <nav class="nav-band">
    <div class="nav-item" style="left:46px">
      <div class="bubble"><svg width="34" height="34" viewBox="0 0 34 34"><rect x="3" y="4" width="28" height="20" rx="2" fill="none" stroke="#4a4f52" stroke-width="3"/><polyline points="7,15 12,15 14,10 17,19 20,13 27,13" fill="none" stroke="#4a4f52" stroke-width="2"/><rect x="14" y="24" width="6" height="5" fill="#4a4f52"/><rect x="9" y="29" width="16" height="3" fill="#4a4f52"/></svg></div>
      My<br>Confirmation
    </div>
    <div class="nav-item" style="left:141px">
      <div class="bubble"><div class="figure-fill" role="img" aria-label="Microscope icon" style="background:#5a5f62;width:30px;height:38px;border-radius:6px"></div></div>
      My<br>Nearest Lab
    </div>
    <div class="nav-item" style="left:234px">
      <div class="bubble"><div class="figure-fill" role="img" aria-label="DNA strand icon" style="background:linear-gradient(#5a5f62,#7a7f82);width:18px;height:40px;border-radius:9px"></div></div>
      My Orders
    </div>
    <div class="nav-item" style="left:328px">
      <div class="bubble"><svg width="32" height="36" viewBox="0 0 32 36"><rect x="3" y="4" width="26" height="30" rx="2" fill="none" stroke="#4a4f52" stroke-width="3"/><rect x="10" y="1" width="12" height="6" rx="1" fill="#4a4f52"/><polyline points="7,21 12,21 14,15 17,26 20,18 25,18" fill="none" stroke="#4a4f52" stroke-width="2"/></svg></div>
      My Results
    </div>
    <div class="nav-item" style="left:419px">
      <div class="bubble"><svg width="30" height="36" viewBox="0 0 30 36"><rect x="2" y="4" width="26" height="30" rx="2" fill="none" stroke="#4a4f52" stroke-width="3"/><rect x="9" y="1" width="12" height="6" rx="1" fill="#4a4f52"/><g fill="#4a4f52"><rect x="7" y="12" width="3" height="3"/><rect x="12" y="12" width="11" height="3"/><rect x="7" y="18" width="3" height="3"/><rect x="12" y="18" width="11" height="3"/><rect x="7" y="24" width="3" height="3"/><rect x="12" y="24" width="11" height="3"/></g></svg></div>
      My Receipts
    </div>
    <div class="nav-item is-active" style="left:511px">
      <div class="bubble"><div class="figure-fill" role="img" aria-label="Doctor figure icon" style="background:linear-gradient(#3d8fd3,#1e6fb3)"></div></div>
      My Account
    </div>
    <div class="nav-item" style="left:606px">
      <div class="bubble"><svg width="36" height="26" viewBox="0 0 36 26"><rect x="1" y="1" width="34" height="24" fill="#4a4f52"/><polyline points="2,2 18,15 34,2" fill="none" stroke="#9aa0a3" stroke-width="2"/></svg></div>
      <span class="badge">2</span>
      My Inbox
    </div>
    <div class="nav-item" style="left:701px">
      <div class="bubble"><div class="figure-fill" role="img" aria-label="Support agent figure icon" style="background:#4a4f52;width:38px"></div></div>
      Contact Us
    </div>
    <span class="nav-pointer"></span>
  </nav>

  <main class="panel">
    <section class="card card-info">
      <h2 class="card-title">Edit Personal Info</h2>
      <div class="field" style="left:26px;top:57px;width:261px">Harlow</div>
      <div class="field" style="left:316px;top:57px;width:261px">Dana</div>
      <div class="field" style="left:26px;top:99px;width:261px">555-014-2270</div>
      <div class="field" style="left:316px;top:99px;width:261px">dana@mailbrook.com</div>
      <div class="field" style="left:26px;top:142px;width:554px">Address</div>
      <div class="field select" style="left:26px;top:184px;width:84px">Sep</div>
      <div class="field select" style="left:114px;top:184px;width:81px">11</div>
      <div class="field select" style="left:203px;top:184px;width:91px">1984</div>
      <div class="radio" style="left:319px"><i></i>Male</div>
      <div class="radio is-checked" style="left:382px"><i></i>Female</div>
      <div class="button" style="left:28px;top:237px">save changes</div>
    </section>

    <section class="card card-password">
      <h2 class="card-title">Edit Password</h2>
      <div class="field-label" style="top:62px">Old Password</div>
      <div class="field-label" style="top:102px">New Password</div>
      <div class="field-label" style="top:142px">Retype Password</div>
      <div class="field" style="left:176px;top:55px;width:260px"></div>
      <div class="field" style="left:176px;top:95px;width:260px"></div>
      <div class="field" style="left:176px;top:135px;width:260px"></div>
      <div class="button" style="left:178px;top:185px">save changes</div>
    </section>
  </main>

</div>
</body>
</html>
```